New Business Card for our Indoor Golf Training Facility

We are looking for designs for a new business card for our indoor golf training facility. Attached is our logo, our logo with our slogan, and here is our elevator pitch (What makes us different from the others) not sure if all the info will fit on one card, maybe you can condense the elevator pitch? here is the info

Elevator Pitch
We work with serious golfers and those that want to be serious golfers…
to make you better, faster, at all phases of the game…
We use the same state-of-the-art technology as professional golfers…
which produces data sets that shows your improvement in real time.
Our facility is available 24/7 to our members, which allows you to improve on your time.

our website: www.birchpinlinks.com

Target Market(s)

Golfers

Font styles to use
Serif
Sans Serif

Colors
ec1f27
f59195
fbd4d5
919191
d3d3d3
1b1b1b

Requirements
Must have
• our logo or our logo with the slogan, elevator pitch (can be condensed or shortened)

```html
<!DOCTYPE html>
<html lang="en">
<head>
<meta charset="utf-8">
<title>Birch Pin Links – Business Card</title>
<link href="https://fonts.googleapis.com/css2?family=Roboto:wght@400;500;700&family=Roboto+Condensed:wght@400;700&display=swap" rel="stylesheet">
<style>
  :root {
    --brand-red: #ec3d36;
    --white: #ffffff;
    --card-grey: #8e8e8e;
    --backdrop: #2a2a2a;
  }
  * { margin: 0; padding: 0; box-sizing: border-box; }
  html, body { width: 1200px; height: 960px; overflow: hidden; }
  body {
    position: relative;
    background: var(--backdrop);
    font-family: "Roboto", Arial, sans-serif;
  }
  .card {
    position: absolute;
    width: 598px;
    height: 342px;
    border-radius: 18px;
    overflow: hidden;
  }
  .card-front { left: 322px; top: 110px; background: var(--brand-red); }
  .card-back { left: 320px; top: 494px; background: var(--card-grey); color: var(--white); text-align: center; }

  .front-shape { position: absolute; inset: 0; }

  .contact-block { position: absolute; left: 26px; top: 91px; color: var(--white); }
  .contact-name { font-size: 21px; font-weight: 500; line-height: 24px; letter-spacing: .2px; }
  .contact-title { font-size: 14px; font-weight: 500; line-height: 16px; }
  .contact-address { margin-top: 18px; font-size: 14.5px; line-height: 17px; }
  .contact-list { list-style: none; margin-top: 9px; font-size: 14.5px; line-height: 19px; }
  .contact-list li { display: flex; align-items: center; gap: 8px; }
  .contact-list svg { width: 14px; height: 14px; flex: none; }

  .brand { position: absolute; left: 300px; top: 148px; color: var(--brand-red); }
  .brand-row { display: flex; align-items: center; gap: 8px; }
  .brand-mark { width: 38px; height: 38px; border: 3px solid var(--brand-red); border-radius: 50%; }
  .brand-name { font-size: 31px; font-weight: 500; line-height: 40px; }
  .brand-slogan { margin: 1px 0 0 62px; font-size: 10.5px; line-height: 12px; }

  .back-ring {
    position: absolute; left: 241px; top: 39px;
    width: 112px; height: 112px;
    border: 7px solid var(--white); border-radius: 50%;
  }
  .pitch-heading {
    position: absolute; left: 0; right: 0; top: 176px;
    font-size: 19px; font-weight: 700; letter-spacing: .3px;
  }
  .pitch-text {
    position: absolute; left: 0; right: 0; top: 204px;
    font-family: "Roboto Condensed", Arial, sans-serif;
    font-size: 14.8px; line-height: 18px;
  }
  .social-dots { position: absolute; left: 280px; top: 303px; display: flex; gap: 4px; }
  .social-dots span { width: 18px; height: 18px; border-radius: 50%; background: var(--white); }
</style>
</head>
<body>

<section class="card card-front">
  <svg class="front-shape" viewBox="0 0 598 342" aria-hidden="true">
    <circle cx="425" cy="170" r="181" fill="none" stroke="var(--white)" stroke-width="2"/>
    <circle cx="425" cy="170" r="172" fill="var(--white)"/>
    <rect x="425" y="0" width="173" height="342" fill="var(--white)"/>
  </svg>

  <div class="contact-block">
    <p class="contact-name">DANA WHITFIELD</p>
    <p class="contact-title">CEO/FOUNDER</p>
    <p class="contact-address">1480 W. Alder Rd. Unit B4<br>Maplecrest, OH 45390</p>
    <ul class="contact-list">
      <li>
        <svg viewBox="0 0 24 24"><path fill="#fff" d="M6.6 10.8a15.1 15.1 0 0 0 6.6 6.6l2.2-2.2a1 1 0 0 1 1-.25 11.4 11.4 0 0 0 3.6.57 1 1 0 0 1 1 1V20a1 1 0 0 1-1 1A17 17 0 0 1 3 4a1 1 0 0 1 1-1h3.5a1 1 0 0 1 1 1c0 1.25.2 2.45.57 3.57a1 1 0 0 1-.25 1z"/></svg>
        555-204-7781
      </li>
      <li>
        <svg viewBox="0 0 24 24"><path fill="#fff" d="M3 5h18v14H3z"/><path fill="none" stroke="var(--brand-red)" stroke-width="2" d="M3 6l9 7 9-7"/></svg>
        info@birchpinlinks.com
      </li>
      <li>
        <svg viewBox="0 0 24 24"><circle cx="12" cy="12" r="10" fill="#fff"/><path fill="none" stroke="var(--brand-red)" stroke-width="1.6" d="M2 12h20M12 2c3 3 3 17 0 20M12 2c-3 3-3 17 0 20"/></svg>
        www.birchpinlinks.com
      </li>
    </ul>
  </div>

  <div class="brand">
    <div class="brand-row">
      <span class="brand-mark"></span>
      <span class="brand-name">Birch Pin Links</span>
    </div>
    <p class="brand-slogan">Indoor Training. Real Data. Any Hour.</p>
  </div>
</section>

<section class="card card-back">
  <span class="back-ring"></span>
  <h2 class="pitch-heading">ELEVATOR PITCH :</h2>
  <p class="pitch-text">
    We work with serious golfers and those that want to be serious golfers…<br>
    to make you better, faster, at all phases of the game…<br>
    We use the same state-of-the-art technology as professional golfers…<br>
    which produces data sets that shows your improvement in real time.<br>
    Our facility is available 24/7 to our members, which allows you to improve on your time.
  </p>
  <div class="social-dots"><span></span><span></span></div>
</section>

</body>
</html>
```